Whitcombe Business Card Design

The name of the business is Dario Whitcombe, CPA LLC
The service that we offer is Accounting, Tax & Consulting Services. I need it to have the following items:
Dario Whitcombe, Principal
Phone Number
Email Address
Physical Address

I have attached the company logo, one in black and one in white. Please provide a design in black background and the other in white background. Please include "Accounting, Tax & Consulting Services". I want the business card to be clean and very professional.

```html
<!DOCTYPE html>
<html lang="en">
<head>
<meta charset="utf-8">
<title>Dario Whitcombe, CPA LLC – Business Card</title>
<link href="https://fonts.googleapis.com/css2?family=Lato:wght@400;700&family=Montserrat:wght@500;600&family=Oswald:wght@600&display=swap" rel="stylesheet">
<style>
  :root {
    --bg: #8f8f8f;
    --paper: #ffffff;
    --charcoal: #333335;
    --ink: #2f2f31;
    --grey: #8a8a8a;
    --red: #a3161c;
  }
  * { box-sizing: border-box; margin: 0; padding: 0; }
  html, body { width: 1200px; height: 866px; overflow: hidden; background: var(--bg); }
  .sheet {
    width: 1200px; height: 866px;
    display: flex; flex-direction: column; align-items: center; justify-content: center; gap: 22px;
  }
  .card {
    position: relative; width: 700px; height: 400px; overflow: hidden;
    box-shadow: 0 8px 18px rgba(0,0,0,.35);
  }
  .card--front { background: var(--paper); }
  .card--back { background: var(--charcoal); display: flex; align-items: center; justify-content: center; }

  .brand { display: flex; align-items: center; gap: 14px; }
  .brand__mark { width: 34px; height: 34px; border: 5px solid var(--ink); flex: none; }
  .brand__name {
    font-family: "Montserrat", sans-serif; font-weight: 600; font-size: 22px;
    letter-spacing: 1.5px; color: var(--ink); text-transform: uppercase; white-space: nowrap;
  }
  .brand__sub {
    font-family: "Montserrat", sans-serif; font-weight: 500; font-size: 13px;
    letter-spacing: 3.4px; color: var(--grey); text-transform: uppercase; margin-top: 4px;
  }
  .card--front .brand { position: absolute; left: 300px; top: 62px; }
  .card--front .brand__name { font-size: 18px; }
  .card--front .brand__sub { font-size: 11px; letter-spacing: 2.6px; }

  .card--back .brand__mark { width: 54px; height: 54px; border: 7px solid #fff; }
  .card--back .brand__name { color: #fff; font-size: 26px; }
  .card--back .brand__sub { color: #a9a9a9; font-size: 15px; letter-spacing: 4.6px; }

  .person { position: absolute; left: 40px; top: 80px; }
  .person__name {
    font-family: "Montserrat", sans-serif; font-weight: 500; font-size: 21px;
    letter-spacing: 1.2px; color: var(--ink); text-transform: uppercase;
  }
  .person__name .first { color: var(--red); }
  .person__title { font-family: "Lato", sans-serif; font-size: 15px; color: var(--grey); margin-top: 2px; }

  .rule { position: absolute; left: 40px; right: 40px; top: 158px; height: 1px; background: var(--red); }

  .contact { position: absolute; left: 40px; top: 176px; font-family: "Lato", sans-serif; font-size: 15px; color: var(--ink); list-style: none; }
  .contact li { display: flex; align-items: center; gap: 8px; margin-bottom: 6px; }
  .contact svg { width: 14px; height: 14px; fill: var(--red); flex: none; }

  .address {
    position: absolute; right: 40px; top: 176px; text-align: right;
    font-family: "Lato", sans-serif; font-size: 15px; line-height: 1.45; color: var(--ink); font-style: normal;
  }

  .footer { position: absolute; left: 0; bottom: 0; width: 700px; height: 52px; }
  .footer__tag {
    position: absolute; right: 40px; bottom: 10px;
    font-family: "Oswald", sans-serif; font-weight: 600; font-size: 17px; letter-spacing: .6px;
    color: #fff; text-transform: uppercase;
  }
</style>
</head>
<body>
<main class="sheet">
  <section class="card card--front" aria-label="Business card front">
    <div class="person">
      <p class="person__name"><span class="first">Dario</span> Whitcombe</p>
      <p class="person__title">Principal</p>
    </div>

    <div class="brand">
      <span class="brand__mark"></span>
      <div>
        <p class="brand__name">Dario Whitcombe, CPA, LLC</p>
        <p class="brand__sub">Certified Public Accountant</p>
      </div>
    </div>

    <div class="rule"></div>

    <ul class="contact">
      <li>
        <svg viewBox="0 0 24 24" aria-hidden="true"><path d="M6.6 10.8a15 15 0 0 0 6.6 6.6l2.2-2.2a1 1 0 0 1 1-.25 11.4 11.4 0 0 0 3.6.57 1 1 0 0 1 1 1V20a1 1 0 0 1-1 1A17 17 0 0 1 3 4a1 1 0 0 1 1-1h3.5a1 1 0 0 1 1 1c0 1.25.2 2.45.57 3.57a1 1 0 0 1-.25 1z"/></svg>
        044-555 210 347
      </li>
      <li>
        <svg viewBox="0 0 24 24" aria-hidden="true"><path d="M2 5h20v14H2zm2 2v.5l8 5 8-5V7l-8 5z"/></svg>
        info@whitcombecpa.com
      </li>
    </ul>

    <address class="address">421, Address line goes here<br>45452,Country Name</address>

    <div class="footer">
      <svg width="700" height="52" viewBox="0 0 700 52" aria-hidden="true">
        <path d="M0 14 H150 L160 6 Q164 4 170 4 H700 V52 H0 Z" fill="var(--charcoal)"/>
        <path d="M0 8 H148 L158 0 H0 Z" fill="var(--red)" transform="translate(0,0)"/>
        <rect x="0" y="8" width="150" height="6" fill="var(--red)"/>
      </svg>
      <p class="footer__tag">Accounting, Tax &amp; Consulting Services</p>
    </div>
  </section>

  <section class="card card--back" aria-label="Business card back">
    <div class="brand">
      <span class="brand__mark"></span>
      <div>
        <p class="brand__name">Dario Whitcombe, CPA, LLC</p>
        <p class="brand__sub">Certified Public Accountant</p>
      </div>
    </div>
  </section>
</main>
</body>
</html>
```